Design a Travel and Tourism website

We would like a freelancer to design a website that is essentially easy to use and navigate database providing local information for Travelers about destination countries.

We proposed website would discuss different rates, fees, visa requirement, resort locations, cheap flights, etc. This website should be elegant and modern. Our business name is rovanix.
Some reference websites are zemplorift.ca, brindlefoxhaven.com,
There should be a forum in the website where travell\ers discuss about their first hand tranvel experience to such destinations.

Tourism

```html
<!DOCTYPE html>
<html lang="en">
<head>
<meta charset="utf-8">
<title>Rovanix — Travel &amp; Tourism</title>
<link rel="stylesheet" href="https://fonts.googleapis.com/css2?family=Montserrat:wght@400;500;600;700;800&family=Open+Sans:wght@400;600;700&display=swap">
<style>
:root{
  --navy:#15224f;
  --navy-deep:#0f1a3d;
  --blue:#1d6cc0;
  --blue-bright:#2a86d9;
  --gold:#b8975a;
  --gold-light:#d4b77c;
  --ink:#2b2f3a;
  --muted:#8a8f9c;
  --line:#e2e4ea;
  --paper:#ffffff;
  --soft:#f3f4f7;
}
*{margin:0;padding:0;box-sizing:border-box}
html,body{width:1200px;height:3240px;overflow:hidden}
body{font-family:"Open Sans",Arial,sans-serif;color:var(--ink);background:var(--paper);position:relative}

/* header */
.hero{position:absolute;top:0;left:0;width:1200px;height:420px}
.hero-photo{position:absolute;inset:0;background:linear-gradient(180deg,#5c8fb8 0%,#8fc0d8 35%,#3fa6b4 60%,#d9cfae 85%,#b9a882 100%)}
.hero-shade{position:absolute;inset:0;background:linear-gradient(90deg,rgba(15,26,61,.55) 0%,rgba(15,26,61,.1) 60%,rgba(15,26,61,0) 100%)}
.topbar{position:absolute;top:0;left:0;right:0;height:22px;background:rgba(15,26,61,.85);display:flex;justify-content:space-between;align-items:center;padding:0 60px;font-size:9px;color:#c9cfdd;letter-spacing:.5px}
.topbar .dots{display:flex;gap:6px}
.topbar .dots span{width:10px;height:10px;border-radius:50%;background:#3a4a7a;display:block}
.topbar .right{display:flex;gap:18px}
.navbar{position:absolute;top:22px;left:0;right:0;height:48px;background:var(--navy);display:flex;align-items:center;justify-content:space-between;padding:0 60px}
.nav-group{display:flex;gap:4px}
.nav-group a{font-family:"Montserrat",Arial,sans-serif;font-size:11px;font-weight:700;color:#fff;text-decoration:none;padding:8px 16px;letter-spacing:.5px}
.nav-group a.active{background:var(--gold)}
.brand{position:absolute;left:50%;top:-4px;transform:translateX(-50%);width:170px;height:78px;background:var(--paper);border-radius:0 0 14px 14px;display:flex;align-items:center;justify-content:center;gap:8px}
.brand .mark{width:14px;height:14px;border-radius:50%;background:var(--gold)}
.brand .name{font-family:"Montserrat",Arial,sans-serif;font-weight:700;font-size:26px;color:var(--navy)}
.hero-title{position:absolute;left:60px;top:150px;font-family:"Montserrat",Arial,sans-serif;font-weight:800;font-size:46px;line-height:54px;color:#fff;letter-spacing:1px}
.hero-badge{position:absolute;right:70px;top:110px;width:150px;height:150px;border-radius:50%;background:var(--navy);border:4px solid var(--gold);display:flex;flex-direction:column;align-items:center;justify-content:center;text-align:center;color:#fff;font-family:"Montserrat",Arial,sans-serif}
.hero-badge b{font-size:13px;font-weight:700;line-height:18px}
.hero-badge span{font-size:11px;color:var(--gold-light);margin-top:4px}
.hero-dots{position:absolute;left:50%;bottom:26px;transform:translateX(-50%);display:flex;gap:8px}
.hero-dots i{width:8px;height:8px;border-radius:50%;background:rgba(255,255,255,.5);display:block}
.hero-dots i.on{background:#fff}

/* search */
.search{position:absolute;top:420px;left:0;width:1200px;height:190px;background:var(--navy-deep)}
.search-tabs{position:absolute;top:22px;left:300px;display:flex;gap:2px}
.search-tabs span{font-family:"Montserrat",Arial,sans-serif;font-size:10px;font-weight:700;color:#fff;padding:9px 16px;letter-spacing:.5px}
.search-tabs span.active{background:var(--gold)}
.search-fields{position:absolute;top:66px;left:140px;width:920px;display:flex;gap:10px}
.field label{display:block;font-size:9px;font-weight:700;color:#c9cfdd;letter-spacing:.5px;margin-bottom:5px;white-space:nowrap}
.field .box{height:30px;background:#fff;border-radius:2px;font-size:10px;color:var(--muted);display:flex;align-items:center;padding:0 10px;gap:6px}
.field .box svg{flex:none}
.f-wide{width:190px}.f-mid{width:150px}.f-small{width:80px}
.search-actions{position:absolute;top:130px;left:0;right:0;display:flex;justify-content:center;align-items:center;gap:22px}
.add-car{font-size:10px;font-weight:700;color:#fff;display:flex;align-items:center;gap:6px}
.add-car i{width:12px;height:12px;background:#fff;display:block}
.btn-search{font-family:"Montserrat",Arial,sans-serif;font-size:11px;font-weight:700;color:#fff;background:var(--blue-bright);padding:9px 26px;letter-spacing:.5px}

/* section headings */
.sec-title{position:absolute;left:0;width:1200px;text-align:center;font-family:"Montserrat",Arial,sans-serif;font-weight:700;font-size:32px;letter-spacing:1px}
.sec-tabs{position:absolute;left:0;width:1200px;display:flex;justify-content:center;gap:26px;font-family:"Montserrat",Arial,sans-serif;font-size:10px;font-weight:700;letter-spacing:.5px}

/* destinations */
.destinations{position:absolute;top:610px;left:0;width:1200px;height:720px}
.destinations .sec-title{top:50px;color:var(--navy)}
.destinations .sec-tabs{top:98px;color:var(--muted)}
.destinations .sec-tabs .on{color:var(--gold)}
.tile{position:absolute;overflow:hidden;border:4px solid #fff;box-shadow:0 2px 8px rgba(0,0,0,.15)}
.tile .photo{position:absolute;inset:0}
.tile .cap{position:absolute;left:16px;bottom:14px;font-family:"Montserrat",Arial,sans-serif;font-weight:600;font-size:15px;color:#fff}
.t-ny{left:138px;top:158px;width:222px;height:532px}
.t-ny .photo{background:linear-gradient(180deg,#8c8a86 0%,#5e5b58 50%,#2f2d2c 100%)}
.t-bkk{left:378px;top:170px;width:440px;height:192px}
.t-bkk .photo{background:linear-gradient(135deg,#1f5bb5 0%,#2c78d0 100%)}
.t-bkk .overlay{position:absolute;inset:0;display:flex;flex-direction:column;align-items:center;justify-content:center;color:#fff;text-align:center;padding:0 80px}
.t-bkk .overlay b{font-family:"Montserrat",Arial,sans-serif;font-size:22px;font-weight:600;margin-bottom:8px}
.t-bkk .overlay p{font-size:11px;line-height:16px}
.t-lv{left:378px;top:376px;width:440px;height:314px}
.t-lv .photo{background:linear-gradient(180deg,#1d2448 0%,#6a3a66 40%,#c8573e 70%,#d9a04a 100%)}
.t-hi{left:836px;top:158px;width:222px;height:532px}
.t-hi .photo{background:linear-gradient(180deg,#2c2b3a 0%,#a2432e 45%,#d0883a 75%,#6c3a2a 100%)}

/* hotels */
.hotels{position:absolute;top:1340px;left:0;width:1200px;height:420px;background:linear-gradient(180deg,var(--blue) 0%,#1a5aa6 100%)}
.hotels .sec-title{top:40px;color:#fff}
.hotels .sec-tabs{top:88px;color:#bcd3ee}
.hotels .sec-tabs .on{color:#fff}
.hotel{position:absolute;top:130px;width:296px;height:250px;border:4px solid #fff;overflow:hidden}
.hotel .photo{position:absolute;inset:0}
.hotel .cap{position:absolute;left:0;right:0;bottom:0;padding:12px 14px;background:linear-gradient(0deg,rgba(10,20,50,.8),rgba(10,20,50,0));color:#fff}
.hotel .cap b{font-family:"Montserrat",Arial,sans-serif;font-size:15px;font-weight:600;display:block}
.hotel .cap span{font-size:10px;color:var(--gold-light)}
.h-lon{left:138px}.h-lon .photo{background:linear-gradient(180deg,#b7c9db 0%,#6f89a3 50%,#3d4a5a 100%)}
.h-par{left:452px}.h-par .photo{background:linear-gradient(180deg,#cfd4d9 0%,#a59a86 50%,#5e5547 100%)}
.h-ber{left:766px}.h-ber .photo{background:linear-gradient(180deg,#6d9ad0 0%,#3c5f8f 50%,#1d2c44 100%)}
.arrow{position:absolute;top:240px}

/* forum */
.forum{position:absolute;top:1760px;left:0;width:1200px;height:640px;background:var(--soft)}
.forum .sec-title{top:50px;color:var(--navy)}
.forum .sub{position:absolute;top:98px;left:0;width:1200px;text-align:center;font-size:10px;color:var(--gold);font-weight:600;letter-spacing:.5px}
.forum-table{position:absolute;top:130px;left:140px;width:920px;background:#fff;border-collapse:collapse;font-size:11px}
.forum-table th{background:var(--gold);color:#fff;font-family:"Montserrat",Arial,sans-serif;font-size:10px;font-weight:700;text-align:left;padding:9px 18px;letter-spacing:.5px}
.forum-table th.r,.forum-table td.r{text-align:right}
.forum-table td{padding:13px 18px;border-bottom:1px solid var(--line);vertical-align:top;color:var(--muted);font-size:10px}
.forum-table td.topic{width:520px}
.forum-table td.topic b{display:block;color:var(--gold);font-size:12px;font-weight:600;margin-bottom:3px}
.btn-view{position:absolute;top:510px;left:553px;width:94px;height:30px;background:var(--blue-bright);color:#fff;font-family:"Montserrat",Arial,sans-serif;font-size:10px;font-weight:700;display:flex;align-items:center;justify-content:center;letter-spacing:.5px}

/* newsletter */
.newsletter{position:absolute;top:2420px;left:0;width:1200px;height:150px;background:linear-gradient(90deg,#0f3f86 0%,var(--blue) 60%,#1553a0 100%)}
.newsletter h3{position:absolute;top:34px;left:0;width:1200px;text-align:center;font-family:"Montserrat",Arial,sans-serif;font-size:22px;font-weight:700;color:#fff;letter-spacing:1px}
.newsletter p{position:absolute;top:64px;left:0;width:1200px;text-align:center;font-size:10px;color:#bcd3ee}
.news-form{position:absolute;top:88px;left:380px;display:flex}
.news-form .input{width:350px;height:34px;background:#fff;font-size:11px;color:var(--muted);display:flex;align-items:center;padding:0 14px}
.news-form .btn{width:88px;height:34px;background:var(--gold);color:#fff;font-family:"Montserrat",Arial,sans-serif;font-size:10px;font-weight:700;display:flex;align-items:center;justify-content:center;letter-spacing:.5px}

/* popular links */
.popular{position:absolute;top:2570px;left:0;width:1200px;height:400px}
.popular .sec-title{top:46px;color:var(--ink);font-size:30px}
.links{position:absolute;top:120px;left:140px;width:920px;display:grid;grid-template-columns:repeat(3,290px);column-gap:25px;row-gap:14px}
.links span{height:36px;border:1px solid var(--line);border-radius:18px;display:flex;align-items:center;gap:10px;padding:0 18px;font-size:12px;color:var(--ink)}

/* footer */
.footer{position:absolute;top:2970px;left:0;width:1200px;height:270px;background:linear-gradient(180deg,#ffffff 0%,#eef2f8 40%,#b8cbe4 100%)}
.skyline{position:absolute;left:0;right:0;bottom:0;height:110px;background:linear-gradient(180deg,#3c6fb2 0%,#1e447f 100%)}
.f-brand{position:absolute;top:26px;left:0;width:1200px;display:flex;justify-content:center;align-items:center;gap:8px}
.f-brand .mark{width:12px;height:12px;border-radius:50%;background:var(--gold)}
.f-brand .name{font-family:"Montserrat",Arial,sans-serif;font-weight:700;font-size:26px;color:var(--navy)}
.f-links{position:absolute;top:84px;left:0;width:1200px;display:flex;justify-content:center;gap:22px;font-family:"Montserrat",Arial,sans-serif;font-size:9px;font-weight:700;color:var(--navy);letter-spacing:.5px}
.f-copy{position:absolute;top:104px;left:0;width:1200px;text-align:center;font-size:9px;color:var(--muted)}
.f-social{position:absolute;top:124px;left:0;width:1200px;display:flex;justify-content:center;gap:10px}
.f-social i{width:26px;height:26px;border-radius:50%;background:var(--navy);display:block}
</style>
</head>
<body>

<header class="hero">
  <div class="hero-photo" role="img" aria-label="Tropical beach with turquoise water and long-tail boats"></div>
  <div class="hero-shade"></div>
  <div class="topbar">
    <div class="dots"><span></span><span></span><span></span></div>
    <div class="right"><span>SIGN IN</span><span>MY LIST</span><span>ENGLISH</span></div>
  </div>
  <nav class="navbar">
    <div class="nav-group">
      <a class="active">HOME</a><a>HOLIDAYS</a><a>FLIGHTS</a><a>HOTELS</a>
    </div>
    <div class="brand"><i class="mark"></i><span class="name">Rovanix</span></div>
    <div class="nav-group">
      <a>CARS</a><a>DEALS</a><a>INSURANCE</a><a>EXTRA</a>
    </div>
  </nav>
  <h1 class="hero-title">START YOUR DREAM<br>HOLIDAYS RIGHT HERE</h1>
  <div class="hero-badge"><b>KATA NOI BEACH,<br>THAILAND</b><span>Explore now</span></div>
  <div class="hero-dots"><i class="on"></i><i></i><i></i></div>
</header>

<section class="search">
  <div class="search-tabs">
    <span class="active">FLIGHT+HOTEL</span><span>HOLIDAYS</span><span>FLIGHTS</span><span>HOTELS</span><span>CARS</span><span>INSURANCE</span><span>EXTRAS</span>
  </div>
  <div class="search-fields">
    <div class="field f-wide"><label>FLYING FROM</label><div class="box"><svg width="10" height="10" viewBox="0 0 10 10"><path d="M5 0a3.5 3.5 0 0 0-3.5 3.5C1.5 6 5 10 5 10s3.5-4 3.5-6.5A3.5 3.5 0 0 0 5 0z" fill="#b8975a"/></svg>City or Airport</div></div>
    <div class="field f-wide"><label>FLYING TO</label><div class="box"><svg width="10" height="10" viewBox="0 0 10 10"><path d="M5 0a3.5 3.5 0 0 0-3.5 3.5C1.5 6 5 10 5 10s3.5-4 3.5-6.5A3.5 3.5 0 0 0 5 0z" fill="#b8975a"/></svg>City or Airport</div></div>
    <div class="field f-mid"><label>DEPARTING</label><div class="box"><svg width="10" height="10" viewBox="0 0 10 10"><rect x=".5" y="1.5" width="9" height="8" fill="none" stroke="#b8975a"/><line x1=".5" y1="4" x2="9.5" y2="4" stroke="#b8975a"/></svg>dd/mm/yy</div></div>
    <div class="field f-mid"><label>RETURNING</label><div class="box"><svg width="10" height="10" viewBox="0 0 10 10"><rect x=".5" y="1.5" width="9" height="8" fill="none" stroke="#b8975a"/><line x1=".5" y1="4" x2="9.5" y2="4" stroke="#b8975a"/></svg>dd/mm/yy</div></div>
    <div class="field f-small"><label>ADULTS</label><div class="box">1</div></div>
    <div class="field f-small"><label>CHILDREN 2-11</label><div class="box">0</div></div>
    <div class="field f-small"><label>INFANTS 0-2</label><div class="box">0</div></div>
  </div>
  <div class="search-actions">
    <span class="add-car"><i></i>ADD A CAR</span>
    <span class="btn-search">SEARCH</span>
  </div>
</section>

<section class="destinations">
  <h2 class="sec-title">DESTINATIONS</h2>
  <div class="sec-tabs"><span class="on">TOP DESTINATIONS</span><span>TRENDING DESTINATIONS</span><span>POPULAR DESTINATIONS</span></div>
  <div class="tile t-ny"><div class="photo" role="img" aria-label="New York skyscrapers seen from street level"></div><span class="cap">New York</span></div>
  <div class="tile t-bkk"><div class="photo" role="img" aria-label="Bangkok temple under a blue overlay"></div>
    <div class="overlay"><b>Bangkok</b><p>Golden temples, floating markets and lively night streets await every traveller in this city.</p></div></div>
  <div class="tile t-lv"><div class="photo" role="img" aria-label="Las Vegas welcome sign at sunset"></div><span class="cap">Las Vegas</span></div>
  <div class="tile t-hi"><div class="photo" role="img" aria-label="Hawaiian dancer at a sunset celebration"></div><span class="cap">Hawaii</span></div>
</section>

<section class="hotels">
  <h2 class="sec-title">HOTELS</h2>
  <div class="sec-tabs"><span class="on">LUXURY HOTELS</span><span>CHEAP HOTELS</span><span>POPULAR HOTELS</span></div>
  <svg class="arrow" style="left:90px" width="16" height="28" viewBox="0 0 16 28"><path d="M14 2 2 14l12 12" fill="none" stroke="#fff" stroke-width="3"/></svg>
  <div class="hotel h-lon"><div class="photo" role="img" aria-label="London street with historic buildings"></div><div class="cap"><b>London, UK</b><span>Rooms from £89</span></div></div>
  <div class="hotel h-par"><div class="photo" role="img" aria-label="Grand Paris hotel facade"></div><div class="cap"><b>Paris, France</b><span>Rooms from €95</span></div></div>
  <div class="hotel h-ber"><div class="photo" role="img" aria-label="Berlin skyline with modern towers at dusk"></div><div class="cap"><b>Berlin, Germany</b><span>Rooms from €79</span></div></div>
  <svg class="arrow" style="left:1094px" width="16" height="28" viewBox="0 0 16 28"><path d="M2 2l12 12L2 26" fill="none" stroke="#fff" stroke-width="3"/></svg>
</section>

<section class="forum">
  <h2 class="sec-title">LATEST TRAVEL FORUM</h2>
  <p class="sub">SHARE YOUR TRIP EXPERIENCE HERE</p>
  <table class="forum-table">
    <thead><tr><th>TOPIC</th><th>POSTED ON</th><th class="r">REPLY / VIEWS</th></tr></thead>
    <tbody>
      <tr><td class="topic"><b>Why Hawaii's a hub for entertainment?</b>By: Nadia Brook</td><td>11 Jun 2017 10:55 AM</td><td class="r">Replies: 17<br>Views: 2</td></tr>
      <tr><td class="topic"><b>Why the hottest place in January?</b>By: Orin Vessel</td><td>11 Jun 2017 10:55 AM</td><td class="r">Replies: 17<br>Views: 2</td></tr>
      <tr><td class="topic"><b>Must visit destinations in the world which make you feel better...</b>By: Nadia Brook</td><td>11 Jun 2017 10:55 AM</td><td class="r">Replies: 17<br>Views: 2</td></tr>
      <tr><td class="topic"><b>Why Hawaii's a hub for entertainment?</b>By: Orin Vessel</td><td>11 Jun 2017 10:55 AM</td><td class="r">Replies: 17<br>Views: 2</td></tr>
      <tr><td class="topic"><b>Why the hottest place in January?</b>By: Nadia Brook</td><td>11 Jun 2017 10:55 AM</td><td class="r">Replies: 17<br>Views: 2</td></tr>
    </tbody>
  </table>
  <span class="btn-view">VIEW ALL</span>
</section>

<section class="newsletter">
  <h3>SIGN UP TO OUR NEWSLETTER</h3>
  <p>GET UPDATES FOR SPECIAL OFFERS</p>
  <div class="news-form"><span class="input">Enter your email</span><span class="btn">SUBMIT</span></div>
</section>

<section class="popular">
  <h2 class="sec-title">POPULAR LINKS YOU MAY INTERESTED</h2>
  <div class="links">
    <span><svg width="12" height="10" viewBox="0 0 12 10"><path d="M1 5l3.5 3.5L11 1" fill="none" stroke="#b8975a" stroke-width="2"/></svg>New York Holidays</span>
    <span><svg width="12" height="10" viewBox="0 0 12 10"><path d="M1 5l3.5 3.5L11 1" fill="none" stroke="#b8975a" stroke-width="2"/></svg>Amsterdam Hotels</span>
    <span><svg width="12" height="10" viewBox="0 0 12 10"><path d="M1 5l3.5 3.5L11 1" fill="none" stroke="#b8975a" stroke-width="2"/></svg>Dubai Holidays</span>
    <span><svg width="12" height="10" viewBox="0 0 12 10"><path d="M1 5l3.5 3.5L11 1" fill="none" stroke="#b8975a" stroke-width="2"/></svg>UK Car Hire</span>
    <span><svg width="12" height="10" viewBox="0 0 12 10"><path d="M1 5l3.5 3.5L11 1" fill="none" stroke="#b8975a" stroke-width="2"/></svg>Orlando Flights</span>
    <span><svg width="12" height="10" viewBox="0 0 12 10"><path d="M1 5l3.5 3.5L11 1" fill="none" stroke="#b8975a" stroke-width="2"/></svg>Bangkok Flights</span>
    <span><svg width="12" height="10" viewBox="0 0 12 10"><path d="M1 5l3.5 3.5L11 1" fill="none" stroke="#b8975a" stroke-width="2"/></svg>Sydney Flights</span>
    <span><svg width="12" height="10" viewBox="0 0 12 10"><path d="M1 5l3.5 3.5L11 1" fill="none" stroke="#b8975a" stroke-width="2"/></svg>Hawaii Hotels</span>
    <span><svg width="12" height="10" viewBox="0 0 12 10"><path d="M1 5l3.5 3.5L11 1" fill="none" stroke="#b8975a" stroke-width="2"/></svg>Paris Car Hire</span>
    <span><svg width="12" height="10" viewBox="0 0 12 10"><path d="M1 5l3.5 3.5L11 1" fill="none" stroke="#b8975a" stroke-width="2"/></svg>New York Holidays</span>
    <span><svg width="12" height="10" viewBox="0 0 12 10"><path d="M1 5l3.5 3.5L11 1" fill="none" stroke="#b8975a" stroke-width="2"/></svg>Amsterdam Hotels</span>
    <span><svg width="12" height="10" viewBox="0 0 12 10"><path d="M1 5l3.5 3.5L11 1" fill="none" stroke="#b8975a" stroke-width="2"/></svg>Dubai Holidays</span>
    <span><svg width="12" height="10" viewBox="0 0 12 10"><path d="M1 5l3.5 3.5L11 1" fill="none" stroke="#b8975a" stroke-width="2"/></svg>UK Car Hire</span>
    <span><svg width="12" height="10" viewBox="0 0 12 10"><path d="M1 5l3.5 3.5L11 1" fill="none" stroke="#b8975a" stroke-width="2"/></svg>Orlando Flights</span>
    <span><svg width="12" height="10" viewBox="0 0 12 10"><path d="M1 5l3.5 3.5L11 1" fill="none" stroke="#b8975a" stroke-width="2"/></svg>Bangkok Flights</span>
  </div>
</section>

<footer class="footer">
  <div class="skyline" role="img" aria-label="City skyline with a plane trail, in blue tones"></div>
  <div class="f-brand"><i class="mark"></i><span class="name">Rovanix</span></div>
  <div class="f-links"><span>HOME</span><span>ABOUT US</span><span>CUSTOMER SUPPORT</span><span>FAQ</span><span>TERMS OF USE</span></div>
  <p class="f-copy">© 2024 Rovanix. All rights reserved.</p>
  <div class="f-social"><i></i><i></i><i></i><i></i></div>
</footer>

</body>
</html>
```